Marwick Law Letterhead

We need a new letterhead design for a Law Firm. The address for the law firm is 1475 Calloway Street, Suite 210, Houston, Texas 77041. Phone Number: 832-361-9027; Fax Number: 832-614-7359. The logo is uploaded to the project.

```html
<!DOCTYPE html>
<html lang="en">
<head>
<meta charset="utf-8">
<title>Marwick Law Letterhead</title>
<link href="https://fonts.googleapis.com/css2?family=Cinzel:wght@500&family=Tinos&display=swap" rel="stylesheet">
<style>
  :root {
    --navy: #27306a;
    --red: #d32a2a;
    --paper: #ffffff;
    --backdrop: #a9aaae;
    --watermark: #f2f2f4;
  }
  html, body {
    margin: 0;
    width: 1200px;
    height: 1200px;
    overflow: hidden;
    background: var(--backdrop);
  }
  .letterhead {
    position: absolute;
    left: 226px;
    top: 56px;
    width: 748px;
    height: 1056px;
    background: var(--paper);
    font-family: "Tinos", "Times New Roman", serif;
    color: var(--navy);
  }
  .brand {
    position: absolute;
    left: 0;
    right: 0;
    top: 44px;
    text-align: center;
  }
  .brand-name {
    display: inline-flex;
    align-items: center;
    gap: 10px;
    font-family: "Cinzel", serif;
    font-weight: 500;
    font-size: 32px;
    line-height: 1;
    color: var(--navy);
  }
  .brand-square {
    width: 28px;
    height: 28px;
    background: var(--navy);
  }
  .brand-tagline {
    margin-top: 9px;
    font-size: 7px;
    letter-spacing: 1.3px;
    text-transform: uppercase;
    color: var(--red);
  }
  .watermark {
    position: absolute;
    left: 200px;
    top: 325px;
    width: 410px;
    height: 410px;
    border-radius: 50%;
    background: var(--watermark);
  }
  .footer-rule {
    position: absolute;
    left: 36px;
    width: 676px;
    top: 990px;
    height: 2px;
    background: var(--navy);
  }
  .footer-col {
    position: absolute;
    top: 1001px;
    font-size: 12.5px;
    line-height: 15px;
    font-style: normal;
  }
  .footer-col.contact-phone { left: 36px; }
  .footer-col.contact-web { left: 309px; }
  .footer-col.contact-address { right: 36px; }
  .footer-item {
    display: flex;
    align-items: center;
    gap: 5px;
  }
  .footer-item svg { width: 10px; height: 10px; flex: none; }
</style>
</head>
<body>
  <main class="letterhead">
    <header class="brand">
      <div class="brand-name"><span class="brand-square"></span>Marwick Law</div>
      <div class="brand-tagline">Your recovery is our steady purpose</div>
    </header>

    <div class="watermark" role="img" aria-label="Faint brand mark watermark"></div>

    <div class="footer-rule"></div>

    <div class="footer-col contact-phone">
      <div class="footer-item">
        <svg viewBox="0 0 12 12"><path fill="#d32a2a" d="M2.3 0.6l2 2.2-1 1.4c.8 1.7 2 2.9 3.6 3.6l1.4-1 2.2 2-1.2 1.8C5.4 10.4 1.6 6.6 .6 1.8z"/></svg>
        <span>832-361-9027</span>
      </div>
      <div class="footer-item">
        <svg viewBox="0 0 12 12"><rect x="3" y="0.5" width="6" height="4" fill="#d32a2a"/><rect x="0.5" y="4.5" width="11" height="6.5" rx="1" fill="#d32a2a"/><rect x="2.5" y="7" width="7" height="2" fill="#fff"/></svg>
        <span>832-614-7359</span>
      </div>
    </div>

    <div class="footer-col contact-web">
      <div class="footer-item">
        <svg viewBox="0 0 12 12"><rect x="0.5" y="2.5" width="11" height="7.5" fill="#d32a2a"/><path d="M1 3l5 4 5-4" stroke="#fff" stroke-width="1" fill="none"/></svg>
        <span>office@marwicklaw.com</span>
      </div>
      <div class="footer-item">
        <svg viewBox="0 0 12 12"><circle cx="6" cy="6" r="5.5" fill="#d32a2a"/><path d="M1 6h10M6 .5c-2.5 3-2.5 8 0 11M6 .5c2.5 3 2.5 8 0 11" stroke="#fff" stroke-width=".8" fill="none"/></svg>
        <span>www.marwicklaw.com</span>
      </div>
    </div>

    <address class="footer-col contact-address">
      1475 Calloway Street<br>
      Suite 210, Houston, Texas 77041
    </address>
  </main>
</body>
</html>
```